Kestrel Motion LLC Sports Therapy and Soft Tissue Injury solutions

We are a company that specializes in Sports Therapy, Physical therapy, muscular rehab, nutrition plans, and personal training. Kestrel Motion travels around the country and world treating athletes and people in the workforce that have Soft Tissue injuries. We are legally partnered with VMR(Vantor Muscle Recovery/vantorrecovery.example) in treating endurance athletes ex. SteelRidge triathalon. We educate our patients on how to sustain a healthy lifestyle.We need a web design that has a Home page summarizing our services, a Physical therapy page, a Personal training and nutrition page. Our ultimate goal is to build relationships with fitness centers, training facilities, and companies that are implementing preventative health measures for their employees. We want to incorporate the VMR logo and Steelridge logo attached in the website but, we want to use our own name (Kestrel Motion LLC) as the main draw. We will provide literature for the website.

Target Market(s)

Grindlane training gyms, Fitness centers, Dance studios, Companies looking for Corporate Wellness programs

Industry/Entity Type

Health And Wellness

Number of Pages Required

4 page

Font styles to use
Sans Serif

Requirements
Must have
• Stock Photos of Athletes training. Examples of Endurance Athletes and Cross training. A mesh of as many sports and training methods as possible. We are a new company and don't have many photos. Easy accessibility to change and add text as the company grows. Vantor Muscle recovery logo incorporated in the back ground of the website. Always visible but does not take over the web page
Nice to have
• Sleek and cool, and masculine design. We want the website to stand out without focusing on one individual. We want to use the website to brand the company (Kestrel Motion LLC) with easy access to social media platforms

```html
<!DOCTYPE html>
<html lang="en">
<head>
<meta charset="utf-8">
<title>Nutrition | Kestrel Motion LLC</title>
<link href="https://fonts.googleapis.com/css2?family=Anton&family=Open+Sans:ital,wght@0,400;0,600;0,700;1,400&display=swap" rel="stylesheet">
<style>
:root{
  --ink:#1e1e1e;
  --dark:#161616;
  --dark-2:#2a2a2a;
  --red:#c40000;
  --text:#333;
  --muted:#8a8a8a;
  --line:#e4e4e4;
  --band:#f3f3f3;
  --white:#fff;
}
*{box-sizing:border-box;margin:0;padding:0}
html,body{width:1200px;height:2675px;overflow:hidden;background:var(--white)}
body{position:relative;font-family:"Open Sans",Arial,sans-serif;color:var(--text)}
.display{font-family:"Anton","Oswald",Impact,sans-serif;font-weight:400;text-transform:uppercase;color:var(--ink);letter-spacing:.3px}
.accent{color:var(--red)}
.abs{position:absolute}

/* nav */
.site-nav{position:absolute;left:0;top:0;width:1200px;height:66px;background:var(--dark)}
.brand{position:absolute;left:160px;top:20px;color:var(--white);font-family:"Open Sans",sans-serif;font-weight:700;font-size:18px}
.menu{position:absolute;right:162px;top:0;display:flex;gap:0;list-style:none;height:66px}
.menu li{font-family:"Anton",Impact,sans-serif;color:var(--white);font-size:11px;text-transform:uppercase;letter-spacing:.3px;line-height:66px;padding-left:55px;position:relative}
.menu li.active::after{content:"";position:absolute;left:55px;right:0;bottom:0;height:3px;background:var(--red)}

/* hero */
.hero{position:absolute;left:0;top:66px;width:1200px;height:453px;background:radial-gradient(ellipse at 45% 55%,#7b7b7b 0%,#4a4a4a 40%,#262626 100%)}
.hero-title{position:absolute;left:0;width:1200px;top:226px;text-align:center;color:var(--white);font-size:36px}
.hero-sub{position:absolute;left:340px;width:520px;top:287px;text-align:center;color:var(--white);font-size:15px;line-height:24px;font-weight:600}

/* about */
.about-title{position:absolute;left:160px;top:605px;font-size:24px;line-height:36px}
.about-copy{position:absolute;left:160px;top:692px;width:460px;font-size:11.4px;line-height:20.8px}
.about-photo{position:absolute;left:670px;top:596px;width:368px;height:283px;background:linear-gradient(135deg,#6b5a48 0%,#8a9a5a 45%,#c4463a 70%,#5e4a3a 100%)}

/* newsletter */
.signup-title{position:absolute;left:0;width:1200px;top:966px;text-align:center;font-size:24px}
.signup-sub{position:absolute;left:0;width:1200px;top:1014px;text-align:center;font-style:italic;font-size:14px;color:#444}
.signup-form{position:absolute;left:367px;top:1054px;width:466px;height:43px;display:flex;border:1px solid #d6d6d6}
.signup-form .field{flex:1;font-size:11.5px;color:#444;padding:14px 14px}
.btn{background:var(--red);color:var(--white);font-family:"Anton",Impact,sans-serif;font-size:11.5px;text-transform:uppercase;display:flex;align-items:center;justify-content:center;letter-spacing:.3px}
.signup-form .btn{width:106px}

/* recipes */
.recipes{position:absolute;left:0;top:1143px;width:1200px;height:462px;background:var(--band);border-top:1px solid var(--line);border-bottom:1px solid var(--line)}
.recipes-photo{position:absolute;left:0;top:0;width:660px;height:460px;background:linear-gradient(90deg,#3e6b2a 0%,#6a9a3a 30%,#c6d6a0 62%,var(--band) 100%)}
.recipes-title{position:absolute;left:635px;top:124px;font-size:24px}
.recipes-copy{position:absolute;left:635px;top:180px;width:410px;font-size:11.2px;line-height:21px}
.recipes .btn{position:absolute;left:635px;top:338px;width:98px;height:40px}

/* goodies */
.goodies-title{position:absolute;left:0;width:1200px;top:1658px;text-align:center;font-size:24px}
.card{position:absolute;left:160px;width:878px;height:234px;border:1px solid var(--line);background:var(--white)}
.card-photo{position:absolute;top:-1px;width:274px;height:234px}
.card-body{position:absolute;top:0;width:560px}
.card-title{font-size:17px;margin-top:40px;text-transform:none;letter-spacing:.4px}
.card-copy{font-size:11px;line-height:22px;margin-top:16px}
.stats{display:flex;gap:18px;margin-top:14px;font-size:10px;color:var(--muted)}
.stats span{display:flex;align-items:center;gap:4px}
.stats svg{width:11px;height:11px;fill:var(--muted)}

/* footer */
.footer{position:absolute;left:0;top:2318px;width:1200px;height:357px;background:var(--dark)}
.footer-title{position:absolute;left:160px;top:37px;color:var(--white);font-size:23px}
.footer-form{position:absolute;left:620px;top:37px;width:418px;height:39px;display:flex}
.footer-form .field{flex:1;background:var(--dark-2);color:#bbb;font-size:10.5px;padding:12px 14px}
.footer-form .btn{width:88px}
.footer-rule{position:absolute;left:160px;top:110px;width:878px;height:1px;background:#333}
.col{position:absolute;top:150px}
.col h4{font-family:"Anton",Impact,sans-serif;font-weight:400;color:var(--white);font-size:10.5px;text-transform:uppercase;letter-spacing:.3px;margin-bottom:12px}
.col li{list-style:none;color:#a8a8a8;font-size:11.5px;line-height:23px}
.legal{position:absolute;left:160px;top:315px;color:#aaa;font-size:10.5px}
.social{position:absolute;left:856px;top:312px;display:flex;gap:16px}
.social span{width:16px;height:16px;border-radius:50%;background:var(--white)}
</style>
</head>
<body>

<header class="site-nav">
  <div class="brand">Kestrel Motion LLC</div>
  <ul class="menu">
    <li>Home</li><li>Services</li><li>Physical Therapy</li><li>Personal Training</li><li class="active">Nutrition</li><li>Contact Us</li>
  </ul>
</header>

<section class="hero" role="img" aria-label="Black and white overhead photo of fresh vegetables, chicken and dumbbells on a wooden table"></section>
<h1 class="display hero-title">Nutrition</h1>
<p class="hero-sub">Sed ut perspiciatis unde omnloreis isteit voluaccusantium doloremue lauloredantiumtota mrem aperiameaue sa lauloredub illo.</p>

<h2 class="display about-title">Everything you<br>need to know about <span class="accent">Nutrition</span></h2>
<p class="about-copy">At Kestrel Motion we focus on our ability to train individuals from beginners to elite athletes. We have everything you here to attain your fitness goals! False advertisements, 3 month workout fads, insane diets pills, and Elective Surgery are not the way to a healthy sustainable lifestyle. Affordable training is on a person by person basis and comes with nutrition plans custom mad efor you hit ecterspiciatis unde omnis iste natus sitolu.maque ipsa quae ab illo inventore tot me maperiam, eaque ipsa quae ab illo invntore veritati quasi archite ed ut perspi ciatis unde omnis iste natus sitolu ptatem accusantiumoloremque laudant ium,totmem aperi amaque ipsa quae ab illo inventore veritati.</p>
<div class="about-photo" role="img" aria-label="Green apple, measuring tape and a bowl of salad on a wooden table"></div>

<h2 class="display signup-title">Want to access more nutrition information?</h2>
<p class="signup-sub">Sed ut perspiciatis unde omnis iste natus sitolu ptateccusantiu</p>
<div class="signup-form"><div class="field">Email :</div><div class="btn">Start Now</div></div>

<section class="recipes">
  <div class="recipes-photo" role="img" aria-label="Close-up of a fresh salad with spinach, tomato, corn and a fork"></div>
  <h2 class="display recipes-title">Recipes</h2>
  <p class="recipes-copy">Sed ut perspiciatis unde omnis iste natus sitolu ptatem accusantium doloremque lantium, totme maperiam, eaque ipsa quae ab illo inventore veritati quasi archite ed ut perspiciatis unde omnis iste natus sitolu ptatem accusantium doloremque laudant ium,totmem aperi amaque ipsa quae ab illo inventore veritati quasiar it ectersplciatis unde omnis iste natus sitolu.maque ipsa quae ab illo inventoretot me maperia eaqu ipsa.</p>
  <div class="btn">Read More</div>
</section>

<h2 class="display goodies-title">Other <span class="accent">Goodies</span></h2>

<article class="card" style="top:1735px">
  <div class="card-photo" style="left:-1px;background:linear-gradient(135deg,#d9d4cc,#8a9a6a 55%,#b78a5a)" role="img" aria-label="Hands serving salad onto a plate"></div>
  <div class="card-body" style="left:314px">
    <h3 class="display card-title">At vero eos et accusamus et iusto odio dignis</h3>
    <p class="card-copy">Sed ut perspiciatis unde omnis iste natus sitolu ptatem accusantium doloremque lantium, totme maperiam, eaque ipsa quae ab illo inventore veritati quasi archite ed ut perspiciatis unde omnis iste natus sitolu ptatem accusantium doloremque laudant ium,totmem aperi amaque ipsa quae ab illo inventore veritati quasiar it ectersplciatis unde omnis iste natus sitolu.maque ipsa quae ab illo inventoretotme maperia eaqu ipsa.</p>
    <div class="stats">
      <span><svg viewBox="0 0 12 12"><path d="M6 3C3 3 1 6 1 6s2 3 5 3 5-3 5-3-2-3-5-3zm0 5a2 2 0 110-4 2 2 0 010 4z"/></svg>128</span>
      <span><svg viewBox="0 0 12 12"><path d="M1 2h10v7H4l-3 2z"/></svg>2584</span>
      <span><svg viewBox="0 0 12 12"><circle cx="9" cy="2.5" r="1.8"/><circle cx="9" cy="9.5" r="1.8"/><circle cx="3" cy="6" r="1.8"/><path d="M3 6l6-3.5M3 6l6 3.5" stroke="#8a8a8a" stroke-width="1"/></svg>84</span>
    </div>
  </div>
</article>

<article class="card" style="top:2008px">
  <div class="card-body" style="left:30px">
    <h3 class="display card-title">At vero eos et accusamus et iusto odio dignis</h3>
    <p class="card-copy">Sed ut perspiciatis unde omnis iste natus sitolu ptatem accusantium doloremque lantium, totme maperiam, eaque ipsa quae ab illo inventore veritati quasi archite ed ut perspiciatis unde omnis iste natus sitolu ptatem accusantium doloremque laudant ium,totmem aperi amaque ipsa quae ab illo inventore veritati quasiar it ectersplciatis unde omnis iste natus sitolu.maque ipsa quae ab illo inventoretotme maperia eaqu ipsa.</p>
    <div class="stats">
      <span><svg viewBox="0 0 12 12"><path d="M6 3C3 3 1 6 1 6s2 3 5 3 5-3 5-3-2-3-5-3zm0 5a2 2 0 110-4 2 2 0 010 4z"/></svg>128</span>
      <span><svg viewBox="0 0 12 12"><path d="M1 2h10v7H4l-3 2z"/></svg>2584</span>
      <span><svg viewBox="0 0 12 12"><circle cx="9" cy="2.5" r="1.8"/><circle cx="9" cy="9.5" r="1.8"/><circle cx="3" cy="6" r="1.8"/><path d="M3 6l6-3.5M3 6l6 3.5" stroke="#8a8a8a" stroke-width="1"/></svg>84</span>
    </div>
  </div>
  <div class="card-photo" style="left:606px;background:radial-gradient(circle at 55% 50%,#c87a3a 0%,#e8e4de 45%,#f4f4f4 70%)" role="img" aria-label="Grilled chicken salad on a white plate with a fork"></div>
</article>

<footer class="footer">
  <h2 class="display footer-title">Sign up for the latest news and offers</h2>
  <div class="footer-form"><div class="field">Enter Email Address:</div><div class="btn">Sign Up</div></div>
  <div class="footer-rule"></div>
  <div class="col" style="left:160px"><h4>For Consumers</h4><ul><li>Disclosures</li><li>Investor Relations</li><li>Corporate Governance</li><li>Newsroom</li></ul></div>
  <div class="col" style="left:364px"><h4>Business</h4><ul><li>Partners</li><li>Blog</li><li>Company</li><li>Resources</li></ul></div>
  <div class="col" style="left:530px"><h4>Company</h4><ul><li>Nutrition</li><li>Dietary Science</li><li>Recipe/Food Prep</li><li>Training</li></ul></div>
  <div class="col" style="left:708px"><h4>Help</h4><ul><li>Terms</li><li>Privacy</li><li>Contact us</li></ul></div>
  <div class="col" style="left:858px"><h4>Contact us for programs</h4><ul><li>480 Harlow Crest Blvd Suite 210</li><li>Fairmont, California, 90000</li><li>Phone: (555)014-2287</li></ul></div>
  <p class="legal">© 2017 Kestrel Motion LLC. All Copyrights are Reserved. Terms of Use.Certification # 64684</p>
  <div class="social" aria-label="Social media links"><span></span><span></span><span></span><span></span><span></span><span></span></div>
</footer>

</body>
</html>
```